Simple and Clean business card design

We would like the design to be simple clean and to incorporate our colors.

We are open to your design and talent, we have the dots in our logo as we think of it as data points and we connect data points for people.

We are open to see the great creative and clean design you bring to the table

Contact Information for Business Card

please include: name, position, email, phone and website

Font styles to use
Sans Serif

Requirements
Must have
• my colors incorporated, simplicity
Nice to have
• lots of white space, simplicity
Should not have
• complexicity/ complex art

```html
<!DOCTYPE html>
<html lang="en">
<head>
<meta charset="utf-8">
<title>Quillo — Business Card, Front and Back</title>
<link rel="stylesheet" href="https://fonts.googleapis.com/css2?family=Montserrat:wght@400;700&display=swap">
<style>
  :root {
    --backdrop: #161616;
    --card-front: #ffffff;
    --card-back: #1e1e1e;
    --pattern-tone: #3a3a3a;
    --ink: #111111;
    --muted: #8a8a8a;
    --rule: #c4c4c4;
    --brand-blue: #4f79c4;
    --brand-green: #2faa4f;
    --brand-yellow: #f4c21b;
    --brand-red: #e53b2f;
    --decor-light: #f1f2f5;
  }
  * { margin: 0; padding: 0; box-sizing: border-box; }
  html, body {
    width: 1200px;
    height: 909px;
    overflow: hidden;
    background: var(--backdrop);
    font-family: "Montserrat", sans-serif;
  }
  .stage {
    width: 1200px;
    height: 909px;
    display: flex;
    align-items: center;
    justify-content: center;
    gap: 40px;
  }
  .business-card {
    position: relative;
    width: 540px;
    height: 308px;
    overflow: hidden;
    box-shadow: 0 12px 30px rgba(0,0,0,.5);
  }

  /* Front */
  .card-front { background: var(--card-front); }
  .brand {
    position: absolute;
    left: 38px;
    top: 26px;
    display: flex;
    align-items: center;
    gap: 8px;
  }
  .brand-name {
    font-size: 60px;
    font-weight: 700;
    color: var(--ink);
    letter-spacing: -2px;
    line-height: 1;
  }
  .brand-dot {
    width: 18px;
    height: 18px;
    border-radius: 50%;
    background: var(--brand-blue);
    margin-top: 14px;
  }
  .identity {
    position: absolute;
    left: 38px;
    top: 116px;
  }
  .person-name {
    font-size: 18px;
    font-weight: 700;
    color: var(--ink);
    text-transform: uppercase;
    letter-spacing: .6px;
    line-height: 1.2;
  }
  .person-role {
    font-size: 15px;
    font-weight: 400;
    color: var(--muted);
    line-height: 1.3;
  }
  .colour-band {
    display: flex;
    width: 96px;
    height: 4px;
    margin-top: 10px;
  }
  .colour-band span { flex: 1; }
  .band-blue { background: var(--brand-blue); }
  .band-green { background: var(--brand-green); }
  .band-yellow { background: var(--brand-yellow); }
  .band-red { background: var(--brand-red); }
  .contact-list {
    position: absolute;
    left: 38px;
    top: 196px;
    list-style: none;
  }
  .contact-item {
    display: flex;
    align-items: center;
    gap: 9px;
    font-size: 12.5px;
    color: var(--muted);
    height: 22px;
  }
  .contact-icon { width: 11px; height: 11px; }
  .address {
    position: absolute;
    left: 236px;
    top: 238px;
    display: flex;
    align-items: center;
    gap: 12px;
    font-size: 12.5px;
    color: var(--muted);
    line-height: 1.4;
  }
  .address-divider {
    width: 1.5px;
    height: 32px;
    background: var(--rule);
  }
  .decor-area {
    position: absolute;
    right: 0;
    top: 110px;
    width: 190px;
    height: 198px;
    background: radial-gradient(circle at 55% 60%, var(--decor-light) 0%, rgba(241,242,245,0) 72%);
  }

  /* Back */
  .card-back { background: var(--card-back); }
  .back-pattern {
    position: absolute;
    inset: 0;
    background: radial-gradient(ellipse at 40% 40%, var(--pattern-tone) 0%, var(--card-back) 85%);
  }
  .back-brand {
    position: absolute;
    right: 40px;
    bottom: 34px;
    display: flex;
    align-items: center;
    gap: 6px;
  }
  .back-brand .brand-name {
    font-size: 30px;
    color: #ffffff;
    letter-spacing: -1px;
  }
  .back-brand .brand-dot {
    width: 10px;
    height: 10px;
    margin-top: 8px;
  }
</style>
</head>
<body>
<main class="stage">
  <section class="business-card card-front">
    <div class="brand">
      <span class="brand-name">Quillo</span>
      <span class="brand-dot"></span>
    </div>

    <div class="identity">
      <h1 class="person-name">Marcus Ellery</h1>
      <p class="person-role">Founder/ CEO</p>
      <div class="colour-band" aria-hidden="true">
        <span class="band-blue"></span><span class="band-green"></span><span class="band-yellow"></span><span class="band-red"></span>
      </div>
    </div>

    <ul class="contact-list">
      <li class="contact-item">
        <svg class="contact-icon" viewBox="0 0 24 24" aria-hidden="true"><path fill="#111" d="M6.6 10.8a15.1 15.1 0 0 0 6.6 6.6l2.2-2.2c.3-.3.7-.4 1-.2 1.1.4 2.3.6 3.6.6.6 0 1 .4 1 1V20c0 .6-.4 1-1 1A17 17 0 0 1 3 4c0-.6.4-1 1-1h3.5c.6 0 1 .4 1 1 0 1.3.2 2.5.6 3.6.1.3 0 .7-.2 1z"/></svg>
        555-214-0387
      </li>
      <li class="contact-item">
        <svg class="contact-icon" viewBox="0 0 24 24" aria-hidden="true"><path d="M2 5h20v14H2z M2 5l10 8 10-8" fill="none" stroke="#111" stroke-width="2.4"/></svg>
        m.ellery@quillo.one
      </li>
      <li class="contact-item">
        <svg class="contact-icon" viewBox="0 0 24 24" aria-hidden="true"><circle cx="12" cy="12" r="10" fill="none" stroke="#111" stroke-width="2.4"/><path d="M2 12h20M12 2c3 3 3 17 0 20M12 2c-3 3-3 17 0 20" fill="none" stroke="#111" stroke-width="2"/></svg>
        www.Quillo.one
      </li>
    </ul>

    <div class="address">
      <span class="address-divider"></span>
      <p>18 W. Oak Avenue<br>Larkton, IL 60412</p>
    </div>

    <div class="decor-area" role="img" aria-label="Faint light-grey decorative circles"></div>
  </section>

  <section class="business-card card-back">
    <div class="back-pattern" role="img" aria-label="Dark grey scattered dot pattern across the card back"></div>
    <div class="back-brand">
      <span class="brand-name">Quillo</span>
      <span class="brand-dot"></span>
    </div>
  </section>
</main>
</body>
</html>
```